Your After-Marriage Lantern: Sensible, Everyday Guidance for the Freshly Solo

I need a wraparound book cover design for a ~132-page workbook. Trim size will be 8.5x11 and the book will be on 60# paper. The name of this project is the name and subtitle of the book. Here's the synopsis I've come up with, which should be included on the back cover (without the quote marks):
"So you're divorced. What do you do now? There are probably a whole bunch of
things you never thought of, like:
- Cleaning up and automating your finances
- Making sure your insurance coverages are all correct
- Removing your former spouse's name from your assets and liabilities
- Building your personal team of financial advisors
Are you aware you need to take care of these things, but you don't know where to
start? This workbook is perfect for you. You'll be led, step by step, through detailed
explanations of how to do everything on this list, and much, much more!"
Here's the author bio for the back cover:
"Gordon T. Whitlock, Esq. graduated from Halvern College School of Law in 2002 and has been a practicing trial lawyer in the Metro Atlanta area ever since. Family law has always been a big part of Gordy's practice. Throughout his career, Gordy has helped hundreds of people through their divorce cases, and now through this book, Gordy looks forward to being able to help them after the dust settles."
I have an ISBN bar code ready to go, so leave space for it on the back cover in the bottom right corner (winner will be expected to add the bar code graphic to the finished product).
This will be a print-on-demand book through Brixo's PressNook. They have a sizing template if you want to grab it for yourself.
Primarily divorced women, especially middle-aged and older

```html
<!DOCTYPE html>
<html lang="en">
<head>
<meta charset="utf-8">
<title>Your After-Marriage Lantern – Cover</title>
<link href="https://fonts.googleapis.com/css2?family=Oswald:wght@500;700&family=Crimson+Text:wght@400;600&display=swap" rel="stylesheet">
<style>
  :root {
    --rust: #b9530b;
    --spine: #b55009;
    --ink: #111111;
    --paper: #ffffff;
    --art-light: #f6d08a;
    --art-mid: #d98a2e;
    --art-dark: #8a4a14;
  }
  * { margin: 0; padding: 0; box-sizing: border-box; }
  html, body { width: 1200px; height: 776px; overflow: hidden; background: var(--paper); }
  .cover { position: relative; width: 1200px; height: 776px; background: var(--paper); overflow: hidden; }

  /* Back cover */
  .back { position: absolute; left: 0; top: 0; width: 577px; height: 776px; }
  .back-hook {
    position: absolute; left: 30px; top: 36px; width: 500px;
    font-family: "Crimson Text", serif; font-weight: 400;
    color: var(--rust); font-size: 16.5px; line-height: 24px;
    text-align: center; text-transform: uppercase; letter-spacing: 0.2px;
  }
  .back-body {
    position: absolute; left: 47px; top: 120px; width: 453px;
    font-family: "Crimson Text", serif; color: var(--ink);
    font-size: 16.5px; line-height: 22.5px; text-align: justify;
  }
  .checklist { list-style: none; text-align: left; }
  .checklist li::before { content: "- "; }
  .author-heading {
    position: absolute; left: 47px; top: 362px; width: 453px;
    font-family: "Oswald", sans-serif; font-weight: 700;
    color: var(--rust); font-size: 30px; text-align: center; letter-spacing: 0.3px;
  }
  .author-bio {
    position: absolute; left: 47px; top: 414px; width: 453px;
    font-family: "Crimson Text", serif; color: var(--ink);
    font-size: 16.5px; line-height: 22.5px; text-align: justify;
  }

  /* Spine */
  .spine { position: absolute; left: 577px; top: 0; width: 44px; height: 776px; background: var(--spine); }
  .spine-title, .spine-author {
    position: absolute; left: 50%; white-space: nowrap; color: var(--paper);
    transform-origin: left center;
  }
  .spine-title {
    top: 395px;
    font-family: "Oswald", sans-serif; font-weight: 700; font-size: 19px; letter-spacing: 3px;
    transform: rotate(-90deg) translateY(-50%);
    margin-left: 0;
  }
  .spine-author {
    top: 715px;
    font-family: "Crimson Text", serif; font-size: 27px;
    transform: rotate(-90deg) translateY(-50%);
  }

  /* Front cover */
  .front { position: absolute; left: 621px; top: 0; width: 579px; height: 776px; }
  .title-top {
    position: absolute; left: 50px; top: 30px; width: 490px;
    font-family: "Oswald", sans-serif; font-weight: 700; color: var(--rust);
    font-size: 66px; line-height: 1; text-align: center; letter-spacing: -0.5px;
  }
  .title-your {
    position: absolute; left: 71px; top: 200px;
    font-family: "Oswald", sans-serif; font-weight: 700; color: var(--ink);
    font-size: 26px; line-height: 1;
    transform: rotate(-90deg); transform-origin: left top;
  }
  .title-main {
    position: absolute; left: 102px; top: 116px;
    font-family: "Oswald", sans-serif; font-weight: 700; color: var(--ink);
    font-size: 86px; line-height: 1; letter-spacing: -0.5px;
  }
  .cover-art { position: absolute; left: 54px; top: 220px; width: 464px; height: 305px; }
  .subtitle {
    position: absolute; left: 20px; width: 536px; text-align: center;
    font-family: "Crimson Text", serif; color: var(--rust); text-transform: uppercase;
  }
  .subtitle-lead { top: 536px; font-size: 24px; }
  .subtitle-main { top: 574px; font-size: 33px; font-weight: 600; }
  .front-author {
    position: absolute; left: 20px; top: 692px; width: 536px; text-align: center;
    font-family: "Crimson Text", serif; color: var(--ink); font-size: 37px;
  }
</style>
</head>
<body>
<main class="cover">

  <section class="back">
    <p class="back-hook">So you're divorced. What do you do now?<br>There are probably a whole bunch of<br>things you never thought of, like:</p>
    <div class="back-body">
      <ul class="checklist">
        <li>Cleaning up and automating your finances</li>
        <li>Making sure your insurance coverages are all correct</li>
        <li>Removing your former spouse's name from your assets and liabilities.</li>
        <li>Building your personal team of financial advisors</li>
      </ul>
      <p>Are you aware you need to take care of these things, but you don't know where to start? This workbook is perfect for you. You'll be led, step by step, through detailed explanations of how to do everything on this list, and much, much more.</p>
    </div>
    <h2 class="author-heading">ABOUT THE AUTHOR</h2>
    <p class="author-bio">Gordon T. Whitlock, Esq. graduated from Halvern College School of Law in 2002 and has been a practicing trial lawyer in the Metro Atlanta area ever since. Family law has always been a big part of Gordy's practice. Throughout his career, Gordy has helped hundreds of people through their divorce cases, and now through this book, Gordy looks forward to being able to help them after the dust settles.</p>
  </section>

  <section class="spine">
    <span class="spine-title">YOUR AFTER-MARRIAGE LANTERN</span>
    <span class="spine-author">Gordon T. Whitlock</span>
  </section>

  <section class="front">
    <h1>
      <span class="title-top">AFTER-MARRIAGE</span>
      <span class="title-your">YOUR</span>
      <span class="title-main">LANTERN</span>
    </h1>
    <svg class="cover-art" viewBox="0 0 464 305" role="img" aria-label="Illustration of a small house and a piggy bank resting on a round wooden gavel block, with a wooden judge's gavel in front">
      <defs>
        <radialGradient id="artGlow" cx="50%" cy="55%" r="60%">
          <stop offset="0%" stop-color="var(--art-light)"/>
          <stop offset="60%" stop-color="var(--art-mid)"/>
          <stop offset="100%" stop-color="var(--paper)" stop-opacity="0"/>
        </radialGradient>
      </defs>
      <rect width="464" height="305" fill="url(#artGlow)"/>
    </svg>
    <p class="subtitle subtitle-lead">Sensible, Everyday Guidance for</p>
    <p class="subtitle subtitle-main">The Freshly Solo</p>
    <p class="front-author">Gordon T. Whitlock</p>
  </section>

</main>
</body>
</html>
```